Business Card Design Project

Business Card design based on logo.
Updates

I need business card, letterhead, envelope, and if possible, Powerpoint slide template.

On front of business card: Just logo- and  my name and title:  Harriet Lindqvist, Principal

On reverse-logo and the rest of the contact info:

4871 Quarry Lane
Davis, CA 95618
650-318-2764
hl@brackenstudyworks.example

On letterhead-Just logo at top, at bottom  the rest-very small along the bottom

On PPT slide-just the logo.

I also want to try a few other colors-I like lime/dark grey (not black) but would like to try Sienna, maybe also indigo or bright blue-green.

I forgot to add-

On the business card-switch to vertical on reverse side and put:

Reverse side-switch to vertical and list:

Harriet Lindqvist
Principal
Bracken Study Works, LLC

650-318-2764

4871 Quarry Lane
Davis, CA 95618

Harriet Lindqvist
Principal

650-318-2764

4871 Quarry Lane
Davis, CA 95618

I have another project at the same time-for Stationery. Feel free to submit to that one also.

That one includes letterhead, envelope, PPT slide, folder cover sheet-HL

Industry/Entity Type

Business

Requirements
Must have
• Must use logo-preferably lime green version-with gray, not black or just 2-tone -logo on colored background.

```html
<!DOCTYPE html>
<html lang="en">
<head>
<meta charset="utf-8">
<title>Bracken Study Works – Business Cards</title>
<link rel="stylesheet" href="https://fonts.googleapis.com/css2?family=Bodoni+Moda:wght@500&family=Jost:wght@400;600&display=swap">
<style>
  :root {
    --lime: #99b83c;
    --charcoal: #2b2b2b;
    --slate: #4a4a4f;
    --ink: #3f3f44;
    --paper: #ffffff;
    --backdrop: #8c4a26;
  }
  * { box-sizing: border-box; margin: 0; padding: 0; }
  html, body { width: 1200px; height: 716px; overflow: hidden; }
  body {
    position: relative;
    background: var(--backdrop);
    font-family: "Jost", "Futura", sans-serif;
  }
  .card {
    position: absolute;
    width: 502px;
    height: 287px;
    background: var(--paper);
    overflow: hidden;
  }
  .card--contact { left: 85px;  top: 55px; }
  .card--dark    { left: 622px; top: 60px; background: var(--charcoal); }
  .card--large   { left: 86px;  top: 376px; }
  .card--small   { left: 623px; top: 380px; }

  .brand {
    position: absolute;
    left: 0; right: 0;
    text-align: center;
    font-family: "Bodoni Moda", "Didot", serif;
    font-weight: 500;
    color: var(--ink);
    text-transform: uppercase;
    line-height: 1.05;
  }
  .brand__mark {
    display: block;
    margin: 0 auto 10px;
    background: var(--lime);
  }
  .card--contact .brand { top: 20px; font-size: 26px; letter-spacing: 5px; }
  .card--contact .brand__mark { width: 26px; height: 26px; }
  .card--dark .brand { top: 70px; font-size: 34px; letter-spacing: 6px; color: var(--paper); }
  .card--dark .brand__mark { width: 34px; height: 34px; }
  .card--large .brand { top: 78px; font-size: 44px; letter-spacing: 8px; }
  .card--small .brand { top: 52px; font-size: 32px; letter-spacing: 6px; }
  .card--small .brand__mark { width: 30px; height: 30px; }

  .website {
    position: absolute;
    left: 0; right: 0;
    top: 250px;
    text-align: center;
    font-size: 19px;
    letter-spacing: 2.6px;
    color: var(--ink);
  }
  .card--dark .website { top: 260px; color: var(--paper); }

  .name-bar {
    position: absolute;
    left: 0; right: 0;
    top: 177px; height: 30px;
    background: var(--slate);
    color: var(--paper);
    text-align: center;
    line-height: 30px;
    font-size: 17px;
  }
  .name-bar strong { font-weight: 600; }
  .name-bar .title { font-size: 13px; }

  .contact-band {
    position: absolute;
    left: 0; right: 0;
    top: 211px; bottom: 0;
    background: var(--lime);
    color: var(--paper);
    font-size: 12.5px;
    letter-spacing: .3px;
    text-align: center;
    padding-top: 6px;
  }
  .contact-band p { line-height: 24px; }
  .contact-band span { margin: 0 7px; white-space: nowrap; }
  .icon { width: 10px; height: 10px; vertical-align: -1px; margin-right: 4px; fill: var(--paper); }
</style>
</head>
<body>

<section class="card card--contact">
  <div class="brand"><span class="brand__mark"></span>Bracken<br>Study Works</div>
  <div class="name-bar"><strong>Harriet Lindqvist,</strong> <span class="title">Principal</span></div>
  <div class="contact-band">
    <p>
      <span><svg class="icon" viewBox="0 0 10 10"><path d="M2 0h2l1 3-1.5 1a6 6 0 0 0 2.5 2.5L7 5l3 1v2a2 2 0 0 1-2 2A8 8 0 0 1 0 2a2 2 0 0 1 2-2z"/></svg>650-318-2764</span>
      <span><svg class="icon" viewBox="0 0 10 10"><path d="M0 2h10v6H0z M0 2l5 3.5L10 2" fill="none" stroke="#fff" stroke-width="1.2"/></svg>hl@brackenstudyworks.example</span>
    </p>
    <p><span><svg class="icon" viewBox="0 0 10 10"><circle cx="5" cy="5" r="4.3" fill="none" stroke="#fff" stroke-width="1.2"/><path d="M1 5h8M5 1v8" stroke="#fff" stroke-width="1"/></svg>www.brackenstudyworks.example</span></p>
    <p>4871 Quarry Lane, Davis, CA 95618</p>
  </div>
</section>

<section class="card card--dark">
  <div class="brand"><span class="brand__mark"></span>Bracken<br>Study Works</div>
  <p class="website">www.brackenstudyworks.example</p>
</section>

<section class="card card--large">
  <div class="brand">Bracken<br>Study Works</div>
  <p class="website">www.brackenstudyworks.example</p>
</section>

<section class="card card--small">
  <div class="brand"><span class="brand__mark"></span>Bracken<br>Study Works</div>
  <p class="website">www.brackenstudyworks.example</p>
</section>

</body>
</html>
```